Business card design for Brivo Engineering Tandem

We need a new business card design along with all the necessary to place an order. The company is Brivo Engineering Tandem and we recently updated our logo.

```html
<!DOCTYPE html>
<html lang="en">
<head>
<meta charset="utf-8">
<title>Brivo Engineering Tandem – Business Card</title>
<link href="https://fonts.googleapis.com/css2?family=Montserrat:wght@400;500;600;700&display=swap" rel="stylesheet">
<style>
  :root {
    --backdrop: #3b3b3b;
    --card-white: #ffffff;
    --brand-yellow: #e0b924;
    --brand-grey: #8e8e8e;
    --ink: #333333;
    --back-light: #bdbdbd;
    --back-mid: #4a4a4a;
    --back-dark: #0d0d0d;
  }
  * { margin: 0; padding: 0; box-sizing: border-box; }
  html, body {
    width: 1200px;
    height: 1059px;
    overflow: hidden;
    background: var(--backdrop);
    font-family: "Montserrat", sans-serif;
  }
  .canvas {
    position: relative;
    width: 1200px;
    height: 1059px;
  }
  .card {
    position: absolute;
    border-radius: 24px;
    overflow: hidden;
  }
  .card-front {
    left: 256px;
    top: 100px;
    width: 688px;
    height: 393px;
    background: var(--card-white);
  }
  .card-back {
    left: 253px;
    top: 535px;
    width: 694px;
    height: 397px;
    background: linear-gradient(125deg, var(--back-light) 0%, var(--back-mid) 38%, var(--back-dark) 70%, var(--back-dark) 100%);
  }
  .wordmark {
    position: absolute;
    left: 59px;
    top: 166px;
    display: flex;
    align-items: center;
    gap: 12px;
    color: var(--brand-grey);
    font-weight: 600;
  }
  .wordmark-square {
    width: 46px;
    height: 46px;
    background: var(--brand-yellow);
  }
  .wordmark-text { line-height: 1; }
  .wordmark-name {
    display: block;
    font-size: 44px;
    letter-spacing: 2px;
  }
  .wordmark-sub {
    display: block;
    font-size: 12.5px;
    letter-spacing: 1.6px;
    margin-top: 4px;
  }
  .divider {
    position: absolute;
    left: 367px;
    top: 90px;
    width: 2px;
    height: 213px;
    background: var(--brand-yellow);
  }
  .details {
    position: absolute;
    left: 394px;
    top: 86px;
    color: var(--ink);
  }
  .person-name {
    font-size: 29px;
    font-weight: 700;
    color: var(--brand-yellow);
    letter-spacing: 0.5px;
    line-height: 1.1;
  }
  .person-role {
    font-size: 18px;
    font-weight: 500;
    margin-top: 4px;
  }
  .address {
    font-size: 18px;
    font-weight: 500;
    line-height: 28px;
    margin-top: 14px;
    font-style: normal;
  }
  .contact-list {
    list-style: none;
    margin-top: 12px;
  }
  .contact-item {
    display: flex;
    align-items: center;
    gap: 8px;
    font-size: 18px;
    font-weight: 500;
    height: 27.5px;
  }
  .contact-icon {
    width: 15px;
    height: 15px;
    flex: none;
  }
</style>
</head>
<body>
<main class="canvas">
  <section class="card card-front" aria-label="Business card front">
    <div class="wordmark">
      <span class="wordmark-square"></span>
      <span class="wordmark-text">
        <span class="wordmark-name">BRIVO</span>
        <span class="wordmark-sub">ENGINEERING TANDEM</span>
      </span>
    </div>
    <div class="divider"></div>
    <div class="details">
      <h1 class="person-name">OWEN HARTLEY</h1>
      <p class="person-role">Managing Director</p>
      <address class="address">Your address, City<br>State, Zip 1234</address>
      <ul class="contact-list">
        <li class="contact-item">
          <svg class="contact-icon" viewBox="0 0 16 16" aria-hidden="true"><path fill="#e0b924" d="M1 6c0-2 3-3 7-3s7 1 7 3v1h-3.5V5.5h-7V7H1zM4 8h8l2 6H2z"/></svg>
          123 456 789
        </li>
        <li class="contact-item">
          <svg class="contact-icon" viewBox="0 0 16 16" aria-hidden="true"><path fill="#e0b924" d="M1 3h14v10H1z"/><path fill="none" stroke="#fff" stroke-width="1.3" d="M1.5 3.8 8 9l6.5-5.2"/></svg>
          info@brivotandem.com
        </li>
        <li class="contact-item">
          <svg class="contact-icon" viewBox="0 0 16 16" aria-hidden="true"><circle cx="8" cy="8" r="7" fill="#e0b924"/><path fill="#fff" d="M5 3.5c1.5.5 2 2 1 3s-2 .5-2 2 1.5 2 1 4c-2-1-3-3-3-4.5S3.2 4.4 5 3.5zM10 9c1 0 2 1 1.5 2.5-.5 1-1.5 1.5-2 1 0-1-.5-2 .5-3.5z"/></svg>
          www.brivotandem.com
        </li>
      </ul>
    </div>
  </section>

  <section class="card card-back" role="img" aria-label="Card back: rows of repeated brand symbols in a glossy silver-to-black pattern"></section>
</main>
</body>
</html>
```